Business Card Design Project

After recently finishing a design project for the company logo using markbazaar, it's now time for a business card. Attached to this is the logo.

The requirements for the business card are pretty straightforward:

- A clean, uncomplicated look
- Consistent usage of fonts
- Designs for both single sided and double sided cards
- A modern layout with preferably space to refer to social media accounts and/or downloadable vcards through a qr code
- consistent application of the company colour scheme: red/white. Hex codes for exact colour can be provided

Thanks!

```html
<!DOCTYPE html>
<html lang="en">
<head>
<meta charset="utf-8">
<title>Kiln Street Staffing – Business Cards</title>
<link rel="stylesheet" href="https://fonts.googleapis.com/css2?family=Open+Sans:ital,wght@0,400;0,600;0,700;1,700&display=swap">
<style>
  :root {
    --brand-red: #e31e27;
    --ink: #231f20;
    --text: #333333;
    --slate: #858585;
    --paper: #ffffff;
    --backdrop: #e8e5e1;
  }
  * { margin: 0; padding: 0; box-sizing: border-box; }
  html, body {
    width: 960px; height: 1200px; overflow: hidden;
    background: var(--backdrop);
    font-family: "Open Sans", Arial, sans-serif;
  }
  .sheet { position: relative; width: 960px; height: 1200px; }

  .card {
    position: absolute;
    background: var(--paper);
    border-radius: 28px;
    overflow: hidden;
    box-shadow: 0 4px 10px rgba(0,0,0,0.18);
  }
  .card--front { left: 56px; top: 88px; width: 839px; height: 478px; }
  .card--back  { left: 60px; top: 638px; width: 840px; height: 478px; }

  .swoosh { position: absolute; inset: 0; width: 100%; height: 100%; }
  .swoosh__red  { fill: var(--brand-red); }
  .swoosh__grey { fill: var(--slate); }

  .wordmark { position: absolute; display: flex; align-items: center; }
  .wordmark__square { background: var(--brand-red); flex: none; }
  .wordmark__text { display: flex; flex-direction: column; }
  .wordmark__name {
    color: var(--ink); font-weight: 600; letter-spacing: -1px; line-height: 1;
  }
  .wordmark__tag {
    color: var(--ink); font-weight: 600; line-height: 1;
    letter-spacing: 0.3em; text-transform: uppercase;
  }

  .card--front .wordmark { left: 46px; top: 72px; gap: 24px; }
  .card--front .wordmark__square { width: 72px; height: 72px; }
  .card--front .wordmark__name { font-size: 64px; }
  .card--front .wordmark__tag { font-size: 31px; margin-top: 14px; }

  .card--back .wordmark { left: 136px; top: 168px; gap: 30px; }
  .card--back .wordmark__square { width: 88px; height: 88px; }
  .card--back .wordmark__name { font-size: 80px; }
  .card--back .wordmark__tag { font-size: 39px; margin-top: 16px; }

  .contact { position: absolute; left: 40px; top: 244px; color: var(--text); }
  .contact__person { font-size: 24px; font-weight: 700; margin-bottom: 16px; }
  .contact__role { font-size: 20px; font-weight: 400; }
  .contact__line { font-size: 19px; line-height: 31px; }
  .contact__key { font-weight: 700; font-style: italic; }
  .contact__address { font-size: 19px; line-height: 29px; margin-top: 10px; }
</style>
</head>
<body>
<main class="sheet">

  <section class="card card--front" aria-label="Business card front">
    <svg class="swoosh" viewBox="0 0 839 478" aria-hidden="true">
      <path class="swoosh__red" d="M669,0 C745,55 792,160 784,272 C776,380 725,440 666,478 L839,478 L839,0 Z"/>
      <path class="swoosh__grey" d="M770,178 C788,330 722,430 652,478 L458,478 C625,432 752,330 770,178 Z"/>
    </svg>

    <div class="wordmark">
      <span class="wordmark__square"></span>
      <div class="wordmark__text">
        <span class="wordmark__name">Kiln Street</span>
        <span class="wordmark__tag">Staffing</span>
      </div>
    </div>

    <div class="contact">
      <p class="contact__person">Your Name - <span class="contact__role">Designation</span></p>
      <p class="contact__line"><span class="contact__key">t</span> : 123-123-1234</p>
      <p class="contact__line"><span class="contact__key">e</span> : info@yourwebsite.com</p>
      <p class="contact__line"><span class="contact__key">w</span> : www.kilnstreet.com</p>
      <p class="contact__address">1234, Street Name<br>District, City, Country Code.</p>
    </div>
  </section>

  <section class="card card--back" aria-label="Business card back">
    <div class="wordmark">
      <span class="wordmark__square"></span>
      <div class="wordmark__text">
        <span class="wordmark__name">Kiln Street</span>
        <span class="wordmark__tag">Staffing</span>
      </div>
    </div>
  </section>

</main>
</body>
</html>
```